KR Appraisals website redesign

I would like to refresh my existing website of www.krappraisals-example.com with new graphics, look and feel, as well as updated structure and wording. Content and layout changes have been uploaded to this project Brief.

My existing website has a dark feel. I am now looking for a light and energetic feel. Financial Services is my industry, so the website should be reflect that. I would also like to reflect the concepts of Trust, Service and Expertise.

The website must be serious and upmarket.

Target Market(s)

Corporate board members, CFO's, treasurers and controllers
Auditors, tax advisors, private equity and venture capital asset managers, investors, tax authorities

Industry/Entity Type

Financial Service

Coding

Coded - Design and coding required

Number of Pages Required

5+ page

Font styles to use
Sans Serif
Other font styles liked:
• Designer can choose another modern font

Colors
0355a3
3277b5
85acd3
eaf1f7
f37122
f68d4d
9bcb3c
acd037
cadf82

Requirements
Must have
• Good hi resolution pictures that convey "Finance", "Trust", "Service" or "Expertise".
• An anti-bot (such as Captcha) mechanism in the contact form.
Should not have
• Must not have all content on one rolling screen.

```html
<!DOCTYPE html>
<html lang="en">
<head>
<meta charset="utf-8">
<title>KR Appraisals</title>
<link href="https://fonts.googleapis.com/css2?family=Cinzel:wght@400;600&family=Lato:wght@400;700&display=swap" rel="stylesheet">
<style>
:root{
  --orange:#f37122;
  --orange-soft:#f68d4d;
  --ink:#333;
  --muted:#555;
  --line:#e4e4e4;
  --footer:#3b3b3b;
  --footer-bar:#303030;
  --white:#fff;
  --page:#fafafa;
}
*{box-sizing:border-box;margin:0;padding:0}
html,body{width:1200px;height:2721px;overflow:hidden}
body{position:relative;background:var(--page);font-family:"Lato",sans-serif;color:var(--ink)}
.heading{font-family:"Cinzel",serif;font-weight:400}
.abs{position:absolute}

/* header */
.site-header{left:0;top:0;width:1200px;height:129px;background:var(--white)}
.brand{display:flex;align-items:center;gap:10px;font-family:"Lato",sans-serif;font-size:26px;color:#555;letter-spacing:.5px}
.brand-mark{width:18px;height:18px;background:currentColor}
.site-header .brand{left:80px;top:48px}
.main-nav{left:524px;top:64px;display:flex;gap:48px;font-size:14px;color:#333}
.main-nav .active{color:var(--orange);border-bottom:2px solid var(--orange);padding-bottom:6px}
.call{left:975px;top:56px;display:flex;gap:10px;align-items:center;font-size:13px}
.call-icon{width:28px;height:28px;border-radius:50%;background:var(--orange);display:flex;align-items:center;justify-content:center}
.call small{display:block;color:var(--orange);font-size:12px}

/* hero */
.hero{left:0;top:129px;width:1200px;height:566px;background:linear-gradient(180deg,#0f1216 0%,#23272c 45%,#3a3222 70%,#15171a 100%)}
.hero-title{position:absolute;left:0;right:0;top:262px;text-align:center;color:var(--white);font-size:33px;line-height:38px;letter-spacing:.5px}
.dots{position:absolute;right:40px;top:265px;display:flex;flex-direction:column;gap:9px}
.dots span{width:8px;height:8px;border-radius:50%;background:#ccc}
.dots .on{background:var(--orange)}

/* about */
.about{left:0;top:722px;width:1200px;text-align:center}
.section-title{font-size:31px;color:#333}
.about p{width:760px;margin:0 auto 16px;font-size:13.2px;line-height:16.5px;color:#333}
.btn{display:inline-block;background:var(--orange);color:var(--white);border-radius:22px;font-size:13.5px;text-align:center}
.about .btn{width:162px;height:43px;line-height:43px;margin-top:6px}

/* services */
.card{background:var(--white);box-shadow:0 0 6px rgba(0,0,0,.06);width:325px;height:310px;text-align:center;padding:0 26px;overflow:hidden}
.card .icon{width:96px;height:90px;margin:40px auto 18px;background:linear-gradient(135deg,#4a4a4a 0%,#6a6a6a 60%,var(--orange) 100%);border-radius:8px;opacity:.85}
.card h3{font-size:22px;line-height:28px;color:#333;margin-bottom:8px}
.card p{font-size:13.2px;line-height:16.5px;color:#444}
.card .more{position:absolute;right:6px;bottom:6px;width:62px;height:58px}
.card-intro{background:var(--orange);color:var(--white);text-align:left;padding:0 35px}
.card-intro .intro-mark{width:44px;height:44px;background:var(--white);margin:46px 0 16px}
.card-intro h2{font-size:35px;line-height:42px;margin-bottom:12px}
.card-intro p{color:var(--white);font-weight:700}

/* news */
.news-band{left:0;top:1790px;width:1200px;height:572px;background:linear-gradient(180deg,var(--page) 0%,#eef1f4 55%,#dfe5ea 100%)}
.news-title{left:0;width:1200px;top:1812px;text-align:center}
.news-card{background:var(--white);width:341px;height:361px;padding:10px 12px}
.news-photo{position:relative;height:198px}
.date{position:absolute;left:0;bottom:-14px;width:40px;height:40px;background:#4a4a4a;color:var(--white);font-family:"Cinzel",serif;font-size:13px;line-height:14px;text-align:center;padding-top:6px}
.news-card h4{font-size:13px;margin:42px 4px 8px;color:#333}
.news-card p{font-size:13px;line-height:16px;color:#555;margin:0 4px 12px}
.news-card a{font-size:14px;color:#333;text-decoration:underline;margin-left:4px}

/* footer */
.site-footer{left:0;top:2362px;width:1200px;height:297px;background:var(--footer);color:var(--white)}
.site-footer .brand{position:absolute;left:80px;top:148px;color:var(--white);font-size:28px}
.col{position:absolute;top:58px}
.col h5{font-family:"Cinzel",serif;font-weight:600;font-size:14px;padding-bottom:10px;border-bottom:2px solid var(--orange);display:inline-block;margin-bottom:18px}
.col ul{list-style:none;font-size:13px;line-height:24px}
.col li::before{content:"•";margin-right:12px}
.contact-list li::before{content:none}
.contact-list li{display:flex;gap:12px;align-items:center}
.contact-list li span.ic{width:14px;display:inline-block}
.field{position:absolute;border:1px solid #888;font-size:12.5px;padding:8px 10px;color:#ddd}
.send{position:absolute;left:857px;top:216px;width:167px;height:38px;line-height:38px}
.bottom-bar{left:0;top:2659px;width:1200px;height:62px;background:var(--footer-bar);color:var(--white);font-size:14px}
.bottom-bar .copy{position:absolute;left:78px;top:22px}
.social{position:absolute;right:82px;top:15px;display:flex;gap:15px}
.social span{width:33px;height:33px;border-radius:50%;border:2px solid #ddd}
.social span.on{background:var(--orange);border-color:var(--orange)}
</style>
</head>
<body>

<header class="site-header abs">
  <div class="brand abs"><span class="brand-mark"></span>KR Appraisals</div>
  <nav class="main-nav abs">
    <span class="active">Home</span><span>About</span><span>Services ˅</span><span>News</span><span>Contact</span>
  </nav>
  <div class="call abs">
    <span class="call-icon"><svg width="14" height="14" viewBox="0 0 24 24"><path fill="#fff" d="M6.6 10.8a15 15 0 0 0 6.6 6.6l2.2-2.2a1 1 0 0 1 1-.25 11.4 11.4 0 0 0 3.6.57 1 1 0 0 1 1 1V20a1 1 0 0 1-1 1A17 17 0 0 1 3 4a1 1 0 0 1 1-1h3.5a1 1 0 0 1 1 1c0 1.25.2 2.45.57 3.57a1 1 0 0 1-.25 1z"/></svg></span>
    <div><small>Call Us Now</small>+31 20 555 0192</div>
  </div>
</header>

<section class="hero abs" role="img" aria-label="Night city skyline with lit office towers">
  <h1 class="hero-title heading">Business &amp; Intellectual<br>Property Valuations</h1>
  <div class="dots"><span></span><span class="on"></span><span></span><span></span></div>
</section>

<section class="about abs">
  <h2 class="section-title heading">About us</h2>
  <svg width="150" height="14" viewBox="0 0 150 14" style="display:block;margin:8px auto 24px"><path d="M4 9 Q75 1 146 7" stroke="#333" stroke-width="1.6" fill="none"/><path d="M20 10 Q75 6 130 8" stroke="#333" stroke-width=".8" fill="none"/></svg>
  <p>KR Appraisals, founded in 2012, is a boutique corporate finance practice servicing companies throughout Europe and North America. Our office is located in the Netherland in the Lindenhof Science Park. Our clients come from a broad range of industries with valuations ranging between micro-cap and large-cap.</p>
  <p>KR Appraisals assists companies with valuations of businesses and intellectual property, M&amp;A advisory, business plan coaching and purchase price allocation (PPA). Through our bespoke approach and global network, we customize teams to the needs of our clients.</p>
  <p>Trust, Service and Expertise are the 3 pillars of KR Appraisals. Trust is paramount.<br>Clients rely on KR Appraisals Services...</p>
  <span class="btn">Read More</span>
</section>

<svg width="0" height="0" style="position:absolute"><defs>
  <symbol id="plus" viewBox="0 0 62 58"><path d="M62 0V58H0Z" fill="#f37122"/><path d="M44 30v16M36 38h16" stroke="#fff" stroke-width="2"/></symbol>
</defs></svg>

<div class="card card-intro abs" style="left:79px;top:1098px">
  <div class="intro-mark"></div>
  <h2 class="heading">Our<br>Services</h2>
  <p>Lorem Ipsum is simply dummy text of the printing and typesetting industry. Lorem has been the industry's standard dummy text ever since the 1500s,</p>
</div>
<div class="card abs" style="left:436px;top:1098px">
  <div class="icon" role="img" aria-label="Line icon of a hand holding a coin"></div>
  <h3 class="heading">Business Valuation</h3>
  <p>Lorem Ipsum is simply dummy text of the printing and typesetting industry. Lorem has been the industry's standard dummy text ever since the 1500s,</p>
  <svg class="more"><use href="#plus"/></svg>
</div>
<div class="card abs" style="left:793px;top:1098px">
  <div class="icon" role="img" aria-label="Line icon of gears and scales"></div>
  <h3 class="heading">Intellectual Property Valuation</h3>
  <p>Lorem Ipsum is simply dummy text of the printing and typesetting industry. Lorem has been the industry's standard dummy text ever since the 1500s,</p>
  <svg class="more"><use href="#plus"/></svg>
</div>
<div class="card abs" style="left:79px;top:1436px">
  <div class="icon" role="img" aria-label="Line icon of a plan document with flow arrows"></div>
  <h3 class="heading">Business Plan Coaching</h3>
  <p>Lorem Ipsum is simply dummy text of the printing and typesetting industry. Lorem has been the industry's standard dummy text ever since the 1500s,</p>
  <svg class="more"><use href="#plus"/></svg>
</div>
<div class="card abs" style="left:436px;top:1436px">
  <div class="icon" role="img" aria-label="Line icon of two advisors talking"></div>
  <h3 class="heading" style="margin-top:30px">M&amp;A Advisory</h3>
  <p style="margin-top:16px">Lorem Ipsum is simply dummy text of the printing and typesetting industry. Lorem has been the industry's standard dummy text ever since the 1500s,</p>
  <svg class="more"><use href="#plus"/></svg>
</div>
<div class="card abs" style="left:793px;top:1436px">
  <div class="icon" role="img" aria-label="Line icon of a pie chart with a coin"></div>
  <h3 class="heading">Purchase Price Allocation</h3>
  <p>Lorem Ipsum is simply dummy text of the printing and typesetting industry. Lorem has been the industry's standard dummy text ever since the 1500s,</p>
  <svg class="more"><use href="#plus"/></svg>
</div>

<div class="news-band abs" role="img" aria-label="Faint pale city skyline backdrop"></div>
<h2 class="news-title section-title heading abs">Latest News</h2>

<article class="news-card abs" style="left:69px;top:1870px">
  <div class="news-photo" role="img" aria-label="Businessman celebrating at laptop in bright office" style="background:linear-gradient(135deg,#e9ecef,#c9ced3 50%,#3a3a3c)"><span class="date">02<br>Oct</span></div>
  <h4 class="heading">What is Lorem Ipsum?</h4>
  <p>Lorem ipsum dolor sit amet, consectetur adipiscing elit, sed do eiusmod tempor incididunt ut labore et dolore magna aliqua.</p>
  <a>Read More</a>
</article>
<article class="news-card abs" style="left:426px;top:1870px">
  <div class="news-photo" role="img" aria-label="Hand pointing at charts on a tablet" style="background:linear-gradient(135deg,#1d3550,#4d7aa3 55%,#b6cde0)"><span class="date">02<br>Oct</span></div>
  <h4 class="heading">What is Lorem Ipsum?</h4>
  <p>Lorem Ipsum is simply dummy &nbsp;the printing and typesetting industry. Lorem Ipsum has been the standard dummy.</p>
  <a>Read More</a>
</article>
<article class="news-card abs" style="left:787px;top:1870px">
  <div class="news-photo" role="img" aria-label="Two colleagues reviewing papers at a desk" style="background:linear-gradient(135deg,#dfe3e6,#9bb0c4 50%,#3b4a5e)"><span class="date">02<br>Oct</span></div>
  <h4 class="heading">What is Lorem Ipsum?</h4>
  <p>Lorem Ipsum is simply dummy &nbsp;the printing and typesetting industry. Lorem Ipsum has been the standard dummy.</p>
  <a>Read More</a>
</article>

<span class="btn abs" style="left:519px;top:2263px;width:162px;height:42px;line-height:42px">View More</span>

<footer class="site-footer abs">
  <div class="brand"><span class="brand-mark"></span>KR Appraisals</div>
  <div class="col" style="left:439px">
    <h5>Quick Link</h5>
    <ul><li>Home</li><li>About</li><li>Services</li><li>News</li><li>Contact</li></ul>
  </div>
  <div class="col" style="left:620px">
    <h5>Quick Contact</h5>
    <ul class="contact-list">
      <li><span class="ic"><svg width="12" height="14" viewBox="0 0 12 14"><path d="M6 13S1 8 1 5a5 5 0 0 1 10 0c0 3-5 8-5 8z" fill="none" stroke="#ccc"/><circle cx="6" cy="5" r="1.7" fill="none" stroke="#ccc"/></svg></span>Kanaalweg 42</li>
      <li><span class="ic"></span>1234 AB Lindenhof</li>
      <li><span class="ic"></span>The Netherlands</li>
      <li><span class="ic"><svg width="14" height="12" viewBox="0 0 14 12"><rect x="1" y="4" width="12" height="7" rx="1" fill="none" stroke="#ccc"/><path d="M2 4 Q7 0 12 4" fill="none" stroke="#ccc"/></svg></span>+31 20 555 0192</li>
      <li><span class="ic"><svg width="14" height="10" viewBox="0 0 14 10"><rect x=".5" y=".5" width="13" height="9" fill="none" stroke="#ccc"/><path d="M.5 .5 7 6l6.5-5.5" fill="none" stroke="#ccc"/></svg></span>info@kr-example.com</li>
    </ul>
  </div>
  <div class="col" style="left:856px">
    <h5>Contact Us</h5>
  </div>
  <div class="field" style="left:857px;top:110px;width:126px;height:32px">Name</div>
  <div class="field" style="left:989px;top:110px;width:128px;height:32px">Phone</div>
  <div class="field" style="left:857px;top:150px;width:260px;height:56px">Message</div>
  <span class="btn send">Send</span>
</footer>

<div class="bottom-bar abs">
  <span class="copy">Copyright © 2019 KR Appraisals. All Right Reserve</span>
  <div class="social"><span class="on"></span><span></span><span></span><span></span></div>
</div>

</body>
</html>
```